Business Card Design Project - del varosi group

dear Sirs

we need business card design for our group ( DEL Varosi Group ) , i have got the Logo design of our group from pixel harbor in previous , so all need details relating to our group i think available with you, as well as the the chosen logo design

we hope to provide us with business card logo that to be appropaite and satisfactory to us .

thanks

note : logo design of our group is attached .
Updates

Reason: please extend the deadline of my project for additional 15 days because i didn't received appropriate design for our gruop yet . kindly beaware that i have received 77 design till now , supossed to send me 200-250 design at least . thanks

Target Market(s)

contents

name : Kerem EL Nadiri

position : Operation Manager

Industry/Entity Type

Business

Requirements
Must have

• person name

group logo
Nice to have
• logo color matching with back background

```html
<!DOCTYPE html>
<html lang="en">
<head>
<meta charset="utf-8">
<title>DEL Varosi Group – Business Card</title>
<link href="https://fonts.googleapis.com/css2?family=Open+Sans:wght@400;600&family=Montserrat:wght@600&display=swap" rel="stylesheet">
<style>
  :root {
    --page: #ecebe8;
    --card-white: #ffffff;
    --brand-blue: #1a5fa6;
    --brand-blue-deep: #0f4a88;
    --brand-blue-light: #3b86cc;
    --highlight: rgba(120, 190, 245, 0.55);
    --ink-dark: #0b2440;
    --rule: #2b2b2b;
    --gold: #e8c45a;
    --text-light: #ffffff;
  }
  * { box-sizing: border-box; margin: 0; padding: 0; }
  html, body { width: 1200px; height: 900px; overflow: hidden; }
  body {
    background: var(--page);
    font-family: "Open Sans", Arial, sans-serif;
    position: relative;
  }
  .card {
    position: absolute;
    left: 285px;
    width: 630px;
    height: 360px;
    border-radius: 4px;
    overflow: hidden;
    box-shadow: 0 6px 18px rgba(0,0,0,0.18);
  }

  /* Back face */
  .card--back {
    top: 50px;
    background:
      radial-gradient(ellipse 55% 45% at 38% 8%, var(--highlight) 0%, rgba(120,190,245,0) 100%),
      linear-gradient(160deg, var(--brand-blue-light) 0%, var(--brand-blue) 45%, var(--brand-blue-deep) 100%);
  }
  .card--back .wordmark {
    position: absolute; left: 0; right: 0; top: 130px;
    display: flex; justify-content: center; align-items: center; gap: 14px;
    color: var(--text-light);
    font-family: "Montserrat", Arial, sans-serif; font-weight: 600;
    font-size: 40px; letter-spacing: 1px;
  }
  .mark-square { width: 26px; height: 26px; flex: none; }
  .card--back .mark-square { background: var(--gold); }
  .card--back .website {
    position: absolute; right: 56px; bottom: 44px;
    color: var(--gold); font-size: 17px; letter-spacing: 0.5px;
  }

  /* Front face */
  .card--front { top: 490px; background: var(--card-white); }
  .front-logo {
    position: absolute; left: 40px; top: 52px;
    display: flex; align-items: center; gap: 14px;
    color: var(--brand-blue);
    font-family: "Montserrat", Arial, sans-serif; font-weight: 600;
    font-size: 40px; letter-spacing: 1px;
  }
  .front-logo .mark-square { background: var(--brand-blue); }
  .front-rule { position: absolute; left: 0; right: 0; top: 186px; height: 4px; background: var(--rule); }
  .info-band {
    position: absolute; left: 0; right: 0; top: 190px; bottom: 0;
    background: var(--brand-blue);
  }
  .person { position: absolute; left: 40px; top: 14px; color: var(--text-light); }
  .person .name { font-size: 24px; font-weight: 400; line-height: 1.25; }
  .person .role { font-size: 16px; color: var(--ink-dark); }
  .address {
    position: absolute; left: 48px; top: 92px;
    color: var(--text-light); font-size: 17px; line-height: 1.2; font-weight: 400;
    font-style: normal;
  }
  .contacts {
    position: absolute; right: 22px; top: 8px;
    list-style: none; color: var(--text-light); font-size: 16.5px;
  }
  .contacts li { display: flex; justify-content: flex-end; align-items: center; gap: 8px; height: 31px; }
  .contacts svg { width: 19px; height: 19px; flex: none; }
</style>
</head>
<body>

<section class="card card--back" aria-label="Business card back">
  <div class="wordmark"><span class="mark-square"></span>DEL VAROSI GROUP</div>
  <p class="website">www.delvarosi.com</p>
</section>

<section class="card card--front" aria-label="Business card front">
  <div class="front-logo"><span class="mark-square"></span>DEL VAROSI GROUP</div>
  <div class="front-rule"></div>
  <div class="info-band">
    <div class="person">
      <p class="name">Kerem EL Nadiri</p>
      <p class="role">Operation Manager</p>
    </div>
    <address class="address">
      P.O. Box: 48210<br>Dubai<br>United Arab Emirates
    </address>
    <ul class="contacts">
      <li>+100 .555 .0142
        <svg viewBox="0 0 20 20" aria-hidden="true"><circle cx="10" cy="10" r="10" fill="#fff"/><path d="M5 8 Q10 4 15 8 L13.5 9.5 L12 8.5 L8 8.5 L6.5 9.5 Z M7 10 H13 L14 14 H6 Z" fill="#1a5fa6"/></svg></li>
      <li>+100 .555 .0143
        <svg viewBox="0 0 20 20" aria-hidden="true"><circle cx="10" cy="10" r="10" fill="#fff"/><rect x="7" y="4" width="6" height="12" rx="1" fill="#1a5fa6"/><rect x="8" y="5.5" width="4" height="5" fill="#fff"/></svg></li>
      <li>+100 .555 .0144
        <svg viewBox="0 0 20 20" aria-hidden="true"><circle cx="10" cy="10" r="10" fill="#fff"/><rect x="5.5" y="5" width="9" height="11" rx="1" fill="#1a5fa6"/><rect x="7" y="6.5" width="6" height="3" fill="#fff"/></svg></li>
      <li>info@delvarosi.com
        <svg viewBox="0 0 20 20" aria-hidden="true"><circle cx="10" cy="10" r="10" fill="#fff"/><rect x="5" y="6.5" width="10" height="7" fill="#1a5fa6"/><path d="M5 6.5 L10 10.5 L15 6.5" fill="none" stroke="#fff" stroke-width="1"/></svg></li>
      <li>www.delvarosi.com
        <svg viewBox="0 0 20 20" aria-hidden="true"><circle cx="10" cy="10" r="10" fill="#fff"/><circle cx="10" cy="10" r="5.5" fill="none" stroke="#1a5fa6" stroke-width="1.2"/><ellipse cx="10" cy="10" rx="2.3" ry="5.5" fill="none" stroke="#1a5fa6" stroke-width="1.2"/><path d="M4.5 10 H15.5" stroke="#1a5fa6" stroke-width="1.2"/></svg></li>
    </ul>
  </div>
</section>

</body>
</html>
```